Namibia currently imports 60% of its food. Harvest Crest Oruva is an initiative which will assist Namibia to become self sustainable in terms of food production. We aim to do this through the development of 3 agricultural production zones which will include farming zones, local farmer assistance, processing and distribution of the final products. Please see our project overview attached.

```html
<!DOCTYPE html>
<html lang="en">
<head>
<meta charset="utf-8">
<title>Harvest Crest Oruva</title>
<link href="https://fonts.googleapis.com/css2?family=Trirong:wght@400;500;600&family=Lato:wght@400;700&display=swap" rel="stylesheet">
<style>
:root{
  --green:#0b6a37;
  --green-dark:#08582d;
  --gold:#c7a27c;
  --mint:#eef8f1;
  --ink:#2b2b2b;
  --blue:#2e86d3;
  --white:#fff;
}
*{box-sizing:border-box;margin:0;padding:0}
html,body{width:1200px;height:4111px;overflow:hidden}
body{font-family:"Lato",sans-serif;color:var(--ink);background:#fff;position:relative}
.serif{font-family:"Trirong",serif}
section,header,footer{position:absolute;left:0;width:1200px}
.abs{position:absolute}
.btn{position:absolute;display:flex;align-items:center;justify-content:center;border-radius:24px;font-family:"Trirong",serif;font-weight:600;font-size:15px;letter-spacing:.5px;box-shadow:3px 4px 0 rgba(0,0,0,.18)}
.btn-light{background:#fff;color:var(--green)}
.btn-green{background:var(--green);color:#fff}
/* header */
.site-header{top:0;height:128px;background:#fff}
.brand{left:95px;top:44px;display:flex;align-items:center;gap:12px;font-family:"Lato",sans-serif;font-weight:700;font-size:26px;color:var(--green)}
.brand-dot{width:26px;height:26px;border-radius:50%;background:var(--green);flex:none}
.contact-item{display:flex;gap:10px;align-items:center;font-family:"Trirong",serif;font-size:12px;color:#444;line-height:1.4}
.contact-item b{font-weight:500;font-size:11px}
.ic{width:24px;height:24px;border-radius:50%;background:var(--green);display:flex;align-items:center;justify-content:center}
.socials{display:flex;gap:9px}
.socials span{width:22px;height:22px;border-radius:50%;background:var(--blue)}
.nav{left:490px;top:88px;display:flex;gap:38px;font-family:"Trirong",serif;font-size:12px;font-weight:500;color:#222}
.nav-cta{left:1002px;top:83px;width:104px;height:28px;border-radius:14px;background:var(--green);color:#fff;font-family:"Trirong",serif;font-size:11px;font-weight:600;display:flex;align-items:center;justify-content:center}
/* hero */
.hero{top:128px;height:592px;background:linear-gradient(180deg,#8fa59a 0%,#6b8a5f 30%,#3f7a34 65%,#2f6d2c 100%)}
.hero-photo{left:0;top:0;width:1200px;height:592px;background:linear-gradient(90deg,rgba(20,50,20,.55) 0%,rgba(20,50,20,.15) 55%,rgba(0,0,0,0) 100%)}
.hero-figure{left:680px;top:70px;width:260px;height:522px;border-radius:120px 120px 0 0;background:linear-gradient(180deg,#4b5a6a,#2d3c4e)}
.hero h2{left:110px;top:110px;color:#fff;font-size:24px;font-weight:500;letter-spacing:1px}
.hero h1{left:108px;top:160px;color:#fff;font-size:66px;font-weight:400;letter-spacing:1px}
.hero .sub{left:110px;top:252px;color:#fff;font-family:"Trirong",serif;font-size:18px;letter-spacing:8px;display:flex;align-items:center;gap:6px}
.hero .sub::after{content:"";width:90px;height:2px;background:#fff}
.hero p{left:110px;top:302px;width:460px;color:#fff;font-size:15px;line-height:31px}
/* needs food */
.needs{top:720px;height:563px;background:var(--green)}
.needs-photo{left:112px;top:86px;width:396px;height:510px;border-radius:0 90px 0 90px;border:3px solid #fff;background:linear-gradient(160deg,#b89a63 0%,#6c8c4a 45%,#2f7a2f 100%)}
.section-title{font-family:"Trirong",serif;font-weight:400;letter-spacing:.5px}
.needs h2{left:600px;top:75px;font-size:39px;color:#fff}
.tag{display:flex;align-items:center;gap:14px;font-family:"Trirong",serif;letter-spacing:5px;font-size:19px}
.needs .tag{left:600px;top:133px;color:#fff}
.needs .tag::after{content:"";width:52px;height:2px;background:#fff}
.needs p{left:598px;top:172px;width:485px;color:#fff;font-size:14px;line-height:26px}
.bullet{position:absolute;left:598px;width:500px;color:#fff;font-size:14px;line-height:31px;text-indent:40px}
.bullet svg{position:absolute;left:0;top:6px}
/* headings centered */
.center-head{width:1200px;text-align:center}
.center-head h2{font-size:39px;color:var(--green)}
.center-tag{justify-content:center;color:var(--gold);margin-top:12px}
.center-tag::before,.center-tag::after{content:"";width:52px;height:2px;background:var(--gold)}
/* zones */
.zones{top:1283px;height:757px;background:#fff}
.zones .center-head{top:92px}
.card{position:absolute;background:#fff;box-shadow:0 2px 10px rgba(0,0,0,.12);text-align:center}
.card.green-edge{border-bottom:4px solid var(--green)}
.card.gold-edge{border-bottom:4px solid var(--gold)}
.zone-card{top:219px;width:287px;height:461px}
.card-photo{position:absolute;left:11px;top:16px;right:11px}
.zone-card .card-photo{height:233px}
.badge{position:absolute;left:115px;top:220px;width:56px;height:56px;border-radius:50%;background:#fff;box-shadow:0 1px 6px rgba(0,0,0,.2);display:flex;align-items:center;justify-content:center}
.card h3{position:absolute;left:0;width:100%;font-family:"Trirong",serif;font-weight:400;font-size:16px;color:#111}
.zone-card h3{top:295px}
.card p{position:absolute;left:0;width:100%;padding:0 14px;font-size:13px;line-height:26px;color:#333}
.zone-card p{top:320px}
.more{position:absolute;left:0;width:100%;font-family:"Trirong",serif;font-size:12px;font-weight:600;color:var(--green);text-decoration:underline;letter-spacing:.5px}
.zone-card .more{top:423px}
/* education */
.education{top:2040px;height:601px;background:linear-gradient(90deg,#2f86d3 0%,#3b90d6 45%,#cfe5ef 72%,#d9e8d8 100%)}
.edu-photo{left:720px;top:0;width:480px;height:601px;background:linear-gradient(180deg,rgba(255,255,255,0) 0%,rgba(180,200,170,.5) 50%,rgba(70,120,60,.75) 100%)}
.edu-people{left:820px;top:80px;width:330px;height:521px;border-radius:140px 140px 0 0;background:linear-gradient(180deg,#8b7a6a,#5b6b7d)}
.education h2{left:110px;top:60px;font-size:39px;color:#fff}
.education .tag{left:110px;top:122px;color:#fff}
.education .tag::after{content:"";width:52px;height:2px;background:#fff}
.quote{left:106px;top:166px;color:#fff;font-weight:700;font-size:14px}
.education p{left:110px;top:198px;width:600px;color:#fff;font-size:13px;line-height:26px}
.edu-list{left:110px;top:320px;display:grid;grid-template-columns:250px 250px;row-gap:16px;color:#fff;font-weight:700;font-size:13px}
.edu-list li{list-style:none;display:flex;align-items:center;gap:12px}
/* solution */
.solution{top:2641px;height:649px;background:#fff}
.solution .center-head{top:62px}
.sol-card{top:184px;width:450px;height:390px}
.sol-card .card-photo{left:13px;right:13px;top:8px;height:218px}
.sol-card h3{top:250px;font-size:18px}
.sol-card p{top:278px;padding:0 26px}
.sol-card .more{top:345px;font-size:13px}
/* newsletter */
.newsletter{top:3290px;height:393px;background:var(--mint)}
.newsletter .center-head{top:60px}
.email-field{left:172px;top:178px;width:853px;height:60px;background:#fff;border-radius:4px;box-shadow:0 1px 4px rgba(0,0,0,.08);font-family:"Trirong",serif;font-size:13px;color:#333;padding:0 17px;display:flex;align-items:center}
/* footer */
.site-footer{top:3683px;height:428px;background:var(--green-dark)}
.foot-brand{left:112px;top:130px;width:260px;font-family:"Lato",sans-serif;font-weight:700;font-size:26px;line-height:34px;color:#fff}
.foot-social{left:112px;top:250px;display:flex;gap:26px}
.foot-social span{width:32px;height:32px;border-radius:50%;background:#fff}
.foot-col{top:95px;color:#fff}
.foot-col h4{font-family:"Trirong",serif;font-weight:500;font-size:18px;margin-bottom:16px}
.foot-col li{list-style:none;font-size:14px;line-height:35px;display:flex;align-items:center;gap:10px}
.contact-row{display:flex;gap:12px;font-size:14px;line-height:27px;margin-bottom:18px;align-items:flex-start}
.foot-ic{width:30px;height:30px;border-radius:50%;background:#fff;display:flex;align-items:center;justify-content:center;flex:none}
.foot-line{left:112px;top:336px;width:976px;height:1px;background:rgba(255,255,255,.45)}
.copyright{top:376px;width:1200px;text-align:center;color:#fff;font-size:14px}
</style>
</head>
<body>

<header class="site-header">
  <div class="abs brand"><span class="brand-dot"></span>Harvest Crest Oruva</div>
  <div class="abs contact-item" style="left:490px;top:16px">
    <span class="ic"><svg width="12" height="12" viewBox="0 0 24 24"><path fill="#fff" d="M6.6 10.8a15 15 0 0 0 6.6 6.6l2.2-2.2c.3-.3.7-.4 1-.2 1.1.4 2.3.6 3.6.6.6 0 1 .4 1 1V20c0 .6-.4 1-1 1A17 17 0 0 1 3 4c0-.6.4-1 1-1h3.5c.6 0 1 .4 1 1 0 1.3.2 2.5.6 3.6.1.3 0 .7-.2 1z"/></svg></span>
    <div><b>Phone:</b><br>+1 555 010 2040</div>
  </div>
  <div class="abs contact-item" style="left:728px;top:14px">
    <span class="ic"><svg width="12" height="12" viewBox="0 0 24 24"><path fill="#fff" d="M3 5h18v14H3z"/><path d="M3 5l9 7 9-7" stroke="#0b6a37" stroke-width="2" fill="none"/></svg></span>
    <div><b>Email:</b><br>info@harvestcrest.org</div>
  </div>
  <div class="abs socials" style="left:985px;top:20px"><span></span><span></span><span></span><span></span></div>
  <nav class="abs nav"><span>HOME</span><span>SUSTAINABILITY</span><span>NEED FOOD</span><span>SOLUTION</span><span>ZONES</span></nav>
  <div class="abs nav-cta">CONTACT US</div>
</header>

<section class="hero">
  <div class="abs hero-photo" role="img" aria-label="Farmer carrying a crate of fresh vegetables across a green field"></div>
  <div class="abs hero-figure" role="img" aria-label="Farmer in checked shirt and apron"></div>
  <h2 class="abs serif">WELCOME TO</h2>
  <h1 class="abs serif">HARVEST CREST</h1>
  <div class="abs sub">ORUVA</div>
  <p class="abs">Namibia is a young democracy in Sub-Saharan Africa with a population of approximately 2.5 Million people.</p>
  <div class="btn btn-light" style="left:111px;top:385px;width:157px;height:46px">GET STARTED</div>
</section>

<section class="needs">
  <div class="abs needs-photo" role="img" aria-label="Farmer in a straw hat reading a tablet among crops"></div>
  <h2 class="abs section-title">NAMIBIA NEEDS FOOD</h2>
  <div class="abs tag">FOOD</div>
  <p class="abs">Namibia is a young democracy in Sub-Saharan Africa with a population of approximately 2.5 Million people. The country's agricultural sector has been slow to keep up with the increasing population. As a consequence, approximately 60% of the foodrequired to feed the nation is imported.</p>
  <div class="bullet" style="top:285px"><svg width="28" height="18" viewBox="0 0 28 18"><path d="M3 16 C8 4 18 1 26 2 C22 10 14 15 3 16Z" fill="none" stroke="#fff" stroke-width="2"/></svg>The elevated cost of these imported foods means a large proportion of the population consume food with low nutritional value.</div>
  <div class="bullet" style="top:355px"><svg width="28" height="18" viewBox="0 0 28 18"><path d="M3 16 C8 4 18 1 26 2 C22 10 14 15 3 16Z" fill="none" stroke="#fff" stroke-width="2"/></svg>Despite vast tracts of available arable land and abundant water resources (both above and below ground), the agricultural sector has struggled to capitalise.</div>
  <div class="btn btn-light" style="left:599px;top:458px;width:156px;height:46px">READ MORE</div>
</section>

<section class="zones">
  <div class="abs center-head">
    <h2 class="section-title">AGRICULTURAL PRODUCTION ZONES</h2>
    <div class="tag center-tag">THREE ZONES</div>
  </div>
  <div class="card zone-card green-edge" style="left:112px">
    <div class="card-photo" role="img" aria-label="Farmers tending rows of leafy crops" style="background:linear-gradient(160deg,#5f9a3e,#2e6a24)"></div>
    <div class="badge"><svg width="26" height="26" viewBox="0 0 24 24" fill="none" stroke="#0b6a37" stroke-width="1.6"><circle cx="12" cy="5" r="2.5"/><path d="M12 8v7M8 11h8M9 21l3-6 3 6"/></svg></div>
    <h3>FARMING ZONES</h3>
    <p>The food production landscape in Namibia which webelieve will empower this beautiful country.</p>
    <div class="more">READ MORE</div>
  </div>
  <div class="card zone-card gold-edge" style="left:456px">
    <div class="card-photo" role="img" aria-label="Two farmers kneeling in a field inspecting soil" style="background:linear-gradient(180deg,#c8cfd6,#8a7a5e 70%,#5a4a36)"></div>
    <div class="badge"><svg width="26" height="26" viewBox="0 0 24 24" fill="none" stroke="#0b6a37" stroke-width="1.6"><path d="M12 22s7-7 7-12a7 7 0 0 0-14 0c0 5 7 12 7 12z"/><circle cx="12" cy="10" r="2.5"/></svg></div>
    <h3>LOCAL FARMER ASSISTANCE</h3>
    <p>The food production landscape in Namibia which webelieve will empower this beautiful country.</p>
    <div class="more">READ MORE</div>
  </div>
  <div class="card zone-card green-edge" style="left:800px">
    <div class="card-photo" role="img" aria-label="Workers harvesting vegetables beside trees" style="background:linear-gradient(180deg,#aac0cf,#6e8a4c 55%,#2e6a24)"></div>
    <div class="badge"><svg width="26" height="26" viewBox="0 0 24 24" fill="none" stroke="#0b6a37" stroke-width="1.6"><circle cx="12" cy="5" r="2.5"/><path d="M12 8v7M8 11h8M9 21l3-6 3 6"/></svg></div>
    <h3>PROCESSING &amp; DISTRIBUTION</h3>
    <p>The food production landscape in Namibia which webelieve will empower this beautiful country.</p>
    <div class="more">READ MORE</div>
  </div>
</section>

<section class="education">
  <div class="abs edu-photo" role="img" aria-label="Field of crops behind two agronomists"></div>
  <div class="abs edu-people" role="img" aria-label="Two agronomists reviewing a tablet in a field"></div>
  <h2 class="abs section-title">HARVEST CREST EDUCATION</h2>
  <div class="abs tag">EDUCATION</div>
  <div class="abs quote">"Give a man a fish and feed him for a day, teach a man&nbsp; to fish and feed him for a lifetime</div>
  <p class="abs">Education is key to empowerment and we embrace that concept.As such, we aim to offer a vocational education scheme for theparticipants in the Harvest Crest Oruva program. We aim tofurnish the participants with the skills to be successful andsustainable farmers in their own rights. Key education outcomes we aim to deliver:</p>
  <ul class="abs edu-list">
    <li><svg width="28" height="18" viewBox="0 0 28 18"><path d="M3 16 C8 4 18 1 26 2 C22 10 14 15 3 16Z" fill="none" stroke="#fff" stroke-width="2"/></svg>Farm Management</li>
    <li><svg width="28" height="18" viewBox="0 0 28 18"><path d="M3 16 C8 4 18 1 26 2 C22 10 14 15 3 16Z" fill="none" stroke="#fff" stroke-width="2"/></svg>Marketing</li>
    <li><svg width="28" height="18" viewBox="0 0 28 18"><path d="M3 16 C8 4 18 1 26 2 C22 10 14 15 3 16Z" fill="none" stroke="#fff" stroke-width="2"/></svg>Crop Management</li>
    <li><svg width="28" height="18" viewBox="0 0 28 18"><path d="M3 16 C8 4 18 1 26 2 C22 10 14 15 3 16Z" fill="none" stroke="#fff" stroke-width="2"/></svg>Computer Skills</li>
    <li><svg width="28" height="18" viewBox="0 0 28 18"><path d="M3 16 C8 4 18 1 26 2 C22 10 14 15 3 16Z" fill="none" stroke="#fff" stroke-width="2"/></svg>Soil Health and Irrigation</li>
    <li><svg width="28" height="18" viewBox="0 0 28 18"><path d="M3 16 C8 4 18 1 26 2 C22 10 14 15 3 16Z" fill="none" stroke="#fff" stroke-width="2"/></svg>Logistics Management</li>
    <li><svg width="28" height="18" viewBox="0 0 28 18"><path d="M3 16 C8 4 18 1 26 2 C22 10 14 15 3 16Z" fill="none" stroke="#fff" stroke-width="2"/></svg>Business Management</li>
    <li><svg width="28" height="18" viewBox="0 0 28 18"><path d="M3 16 C8 4 18 1 26 2 C22 10 14 15 3 16Z" fill="none" stroke="#fff" stroke-width="2"/></svg>Vehicle Mechanics</li>
  </ul>
  <div class="btn btn-light" style="left:110px;top:482px;width:155px;height:46px">READ MORE</div>
</section>

<section class="solution">
  <div class="abs center-head">
    <h2 class="section-title">THE HARVEST CREST SOLUTION</h2>
    <div class="tag center-tag">SOLUTIONS</div>
  </div>
  <div class="card sol-card green-edge" style="left:130px">
    <div class="card-photo" role="img" aria-label="Grain silos behind a field of maize" style="background:linear-gradient(180deg,#9fb9cf 0%,#b9bfc3 45%,#6f9a3a 70%,#3f7a24)"></div>
    <h3>PRIMARY PRODUCTION AREA</h3>
    <p>Primary production will take place on parcels of land secured byHarvest Crest Oruva in the range of 600ha to 3,000ha.</p>
    <div class="more">READ MORE</div>
  </div>
  <div class="card sol-card gold-edge" style="left:618px">
    <div class="card-photo" role="img" aria-label="Farmer checking a tablet in a maize field" style="background:linear-gradient(120deg,#2f5a28,#5f8f3a 50%,#2e6a24)"></div>
    <h3>EMPOWERMENT PRODUCTION AREAS</h3>
    <p>Namibia has a substantial amount of unutilised arable land in possession of either the government, or private individuals</p>
    <div class="more">READ MORE</div>
  </div>
</section>

<section class="newsletter">
  <div class="abs center-head">
    <h2 class="section-title">SIGN UP NEWSLETTER</h2>
    <div class="tag center-tag">CONTACT US</div>
  </div>
  <div class="abs email-field">Enter the email</div>
  <div class="btn btn-green" style="left:520px;top:287px;width:157px;height:46px;font-size:14px">SUBSCRIBE US</div>
</section>

<footer class="site-footer">
  <div class="abs foot-brand">Harvest Crest Oruva</div>
  <div class="abs foot-social"><span></span><span></span><span></span><span></span></div>
  <div class="abs foot-col" style="left:430px">
    <h4>QUICK LINKS</h4>
    <ul>
      <li>&#10140; Home</li><li>&#10140; About</li><li>&#10140; Need Food</li><li>&#10140; Education</li><li>&#10140; Contact Us</li>
    </ul>
  </div>
  <div class="abs foot-col" style="left:663px">
    <h4>HELP LINKS</h4>
    <ul>
      <li>&#10140; FAQ</li><li>&#10140; Terms of use</li><li>&#10140; Privacy Policy</li><li>&#10140; Support Links</li><li>&#10140; Conditions</li>
    </ul>
  </div>
  <div class="abs foot-col" style="left:915px">
    <h4>CONTACT US</h4>
    <div class="contact-row"><span class="foot-ic"><svg width="14" height="14" viewBox="0 0 24 24"><path fill="#08582d" d="M12 2a7 7 0 0 0-7 7c0 5 7 13 7 13s7-8 7-13a7 7 0 0 0-7-7zm0 9.5A2.5 2.5 0 1 1 12 6.5a2.5 2.5 0 0 1 0 5z"/></svg></span><div>HCO<br>Windhoek</div></div>
    <div class="contact-row"><span class="foot-ic"><svg width="13" height="13" viewBox="0 0 24 24"><path fill="#08582d" d="M6.6 10.8a15 15 0 0 0 6.6 6.6l2.2-2.2c.3-.3.7-.4 1-.2 1.1.4 2.3.6 3.6.6.6 0 1 .4 1 1V20c0 .6-.4 1-1 1A17 17 0 0 1 3 4c0-.6.4-1 1-1h3.5c.6 0 1 .4 1 1 0 1.3.2 2.5.6 3.6.1.3 0 .7-.2 1z"/></svg></span><div>+1 555 010 2040</div></div>
    <div class="contact-row"><span class="foot-ic"><svg width="14" height="14" viewBox="0 0 24 24"><path fill="#08582d" d="M3 5h18v14H3z"/><path d="M3 5l9 7 9-7" stroke="#fff" stroke-width="2" fill="none"/></svg></span><div>info@hco.org</div></div>
  </div>
  <div class="abs foot-line"></div>
  <div class="abs copyright">Copyrights@2024.HCO.All Rights Reserved</div>
</footer>

</body>
</html>
```